Meridian Crestline Motors *

Professional business cards for our auto wholesale dealership.

Target Market(s)

New and used cars sales managers and middle class to higher end private party buyers.

Industry/Entity Type

Automotive

Contact Information for Business Card

Meridian Crestline Motors
Darnell R Okonski
Owner
(555) 304-6618
mercrestmotors@quillbox.example
Dealer Lic # 48265

Logo Text

Meridian Crestline Motors, Mer Crest Motors, MCM, etc

Font styles to use
Serif
Sans Serif

Colors

Designer to choose colors to be used in the design.

Requirements
Must have
• A professional, but not pretentious, look
Nice to have
• It might be nice to see "MCM" in a shape form i.e. circle, triangle, etc in the corner or background somehwere
Should not have
• bright "girly" colors

```html
<!DOCTYPE html>
<html lang="en">
<head>
<meta charset="utf-8">
<title>Meridian Crestline Motors — Business Cards</title>
<link href="https://fonts.googleapis.com/css2?family=Open+Sans:wght@400;600;800&display=swap" rel="stylesheet">
<style>
  :root {
    --backdrop: #333436;
    --charcoal: #23272d;
    --charcoal-deep: #1a1d22;
    --lime: #a8cc12;
    --lime-dark: #8fb00c;
    --paper: #f4f4f4;
    --paper-shade: #d9d9d9;
    --ink: #2a2e34;
    --muted: #c9ccd1;
  }
  * { box-sizing: border-box; margin: 0; padding: 0; }
  html, body {
    width: 1200px; height: 1200px; overflow: hidden;
    background: var(--backdrop);
    font-family: "Open Sans", Arial, sans-serif;
  }
  .sheet {
    width: 1200px; height: 1200px;
    display: flex; flex-direction: column; align-items: center; justify-content: center;
    gap: 60px;
  }
  .card {
    position: relative;
    width: 840px; height: 480px;
    border-radius: 26px;
    overflow: hidden;
    box-shadow: 0 18px 40px rgba(0,0,0,.45);
  }

  /* Front */
  .card--front {
    background: linear-gradient(135deg, var(--paper) 0%, #ffffff 40%, var(--paper-shade) 100%);
    display: flex; align-items: center; justify-content: center;
  }
  .wordmark {
    display: flex; align-items: center; gap: 26px;
    color: var(--ink);
    font-weight: 800;
  }
  .wordmark__dot {
    width: 110px; height: 110px; border-radius: 50%;
    background: var(--lime);
    flex: none;
  }
  .wordmark__text { line-height: 1; }
  .wordmark__main { font-size: 60px; letter-spacing: 1px; text-transform: uppercase; }
  .wordmark__sub { font-size: 32px; margin-top: 6px; }

  /* Back */
  .card--back {
    background: linear-gradient(160deg, #2f343b 0%, var(--charcoal) 45%, var(--charcoal-deep) 100%);
    color: #fff;
  }
  .back__band {
    position: absolute; left: 0; right: 0; bottom: 0; height: 26px;
    background: linear-gradient(180deg, var(--lime) 0%, var(--lime-dark) 100%);
  }
  .back__rule {
    position: absolute; left: 0; right: 0; top: 226px; height: 4px;
    background: var(--lime);
  }
  .back__badge {
    position: absolute; left: 470px; top: 98px;
    width: 260px; height: 260px; border-radius: 50%;
    background: var(--lime);
    display: flex; align-items: center; justify-content: center;
    color: var(--charcoal);
    font-weight: 800; font-size: 72px; letter-spacing: 2px;
  }
  .back__brand {
    position: absolute; left: 44px; top: 38px;
    font-weight: 800; line-height: 1;
  }
  .back__brand-main { font-size: 40px; text-transform: uppercase; letter-spacing: .5px; }
  .back__brand-sub { font-size: 24px; margin-top: 4px; }
  .person {
    position: absolute; left: 44px; top: 150px;
    display: flex; align-items: flex-start; gap: 14px;
  }
  .person__pill {
    width: 14px; height: 46px; border-radius: 7px; background: var(--lime);
  }
  .person__name { font-size: 27px; font-weight: 600; line-height: 1.05; }
  .person__role { font-size: 17px; color: var(--muted); }
  .contacts {
    position: absolute; left: 44px; top: 256px;
    list-style: none; font-size: 17px; color: var(--muted);
    display: flex; flex-direction: column; gap: 10px;
  }
  .contacts li { display: flex; align-items: center; gap: 10px; }
  .contacts svg { width: 18px; height: 18px; flex: none; }
  .contacts .licence { padding-left: 0; }
</style>
</head>
<body>
<main class="sheet">

  <section class="card card--front" aria-label="Card front">
    <div class="wordmark">
      <span class="wordmark__dot"></span>
      <div class="wordmark__text">
        <div class="wordmark__main">Meridian</div>
        <div class="wordmark__sub">Crestline Motors</div>
      </div>
    </div>
  </section>

  <section class="card card--back" aria-label="Card back">
    <div class="back__rule"></div>
    <div class="back__badge">MCM</div>
    <div class="back__brand">
      <div class="back__brand-main">Meridian</div>
      <div class="back__brand-sub">Crestline Motors</div>
    </div>
    <div class="person">
      <span class="person__pill"></span>
      <div>
        <div class="person__name">Darnell R Okonski</div>
        <div class="person__role">Owner</div>
      </div>
    </div>
    <ul class="contacts">
      <li>
        <svg viewBox="0 0 24 24" aria-hidden="true"><path fill="var(--lime)" d="M6.6 10.8a15.1 15.1 0 0 0 6.6 6.6l2.2-2.2a1 1 0 0 1 1-.25 11.4 11.4 0 0 0 3.6.57 1 1 0 0 1 1 1V20a1 1 0 0 1-1 1A17 17 0 0 1 3 4a1 1 0 0 1 1-1h3.5a1 1 0 0 1 1 1c0 1.25.2 2.46.57 3.6a1 1 0 0 1-.25 1z"/></svg>
        (555) 304-6618
      </li>
      <li>
        <svg viewBox="0 0 24 24" aria-hidden="true"><rect x="2.5" y="5" width="19" height="14" fill="none" stroke="var(--lime)" stroke-width="2"/><path d="M3 6l9 7 9-7" fill="none" stroke="var(--lime)" stroke-width="2"/></svg>
        mercrestmotors@quillbox.example
      </li>
      <li class="licence">Dealer Lic # 48265</li>
    </ul>
    <div class="back__band"></div>
  </section>

</main>
</body>
</html>
```